Business Card Design

I already have a company logo for my company. I have a logo for the manufacturer we represent. I want a professional business card design.

```html
<!DOCTYPE html>
<html lang="en">
<head>
<meta charset="utf-8">
<title>Beacon Guard LLC – Business Card</title>
<link rel="stylesheet" href="https://fonts.googleapis.com/css2?family=Open+Sans:wght@400;600;700&display=swap">
<style>
  :root {
    --page: #e9e4dc;
    --card-dark: #1c1c1d;
    --card-mid: #2e2e30;
    --gold-light: #b88a33;
    --gold-dark: #8f6a25;
    --red: #d0141c;
    --red-deep: #b80f16;
    --name-red: #e0303a;
    --ink-light: #d9d2c7;
    --ink-muted: #bdb4a6;
    --ink-dark: #1a1a1a;
  }
  * { margin: 0; padding: 0; box-sizing: border-box; }
  html, body {
    width: 1200px; height: 1046px; overflow: hidden;
    background: var(--page);
    font-family: "Open Sans", Arial, sans-serif;
  }
  .card {
    position: absolute; left: 50px; top: 223px;
    width: 1100px; height: 600px;
    border-radius: 40px; overflow: hidden;
    background: radial-gradient(ellipse at 18% 30%, var(--card-mid) 0%, var(--card-dark) 55%, #141415 100%);
    box-shadow: 0 12px 40px rgba(0,0,0,.25);
  }
  .brand {
    position: absolute; top: 120px; left: 0; width: 100%;
    display: flex; align-items: center; justify-content: center; gap: 20px;
  }
  .brand-square { width: 54px; height: 54px; background: var(--red); }
  .brand-name {
    font-weight: 700; font-size: 52px; letter-spacing: 3px;
    color: var(--ink-light); line-height: 1;
  }
  .info-band {
    position: absolute; top: 368px; left: 0; width: 100%; height: 136px;
    background: linear-gradient(90deg, var(--gold-dark) 0%, var(--gold-light) 30%, var(--gold-light) 44%, var(--red-deep) 46%, var(--red-deep) 70%, var(--red) 100%);
  }
  .person { position: absolute; right: 693px; top: 22px; text-align: right; }
  .person-name { font-weight: 600; font-size: 41px; line-height: 1.2; color: var(--ink-light); }
  .person-name .first { color: var(--name-red); }
  .person-title { font-weight: 600; font-size: 28px; color: var(--ink-muted); margin-top: 2px; }
  .band-mark {
    position: absolute; left: 422px; top: 0; width: 266px; height: 136px;
    display: flex; align-items: center; justify-content: center;
    font-weight: 700; font-size: 22px; letter-spacing: 2px; color: var(--ink-dark);
  }
  .contacts { position: absolute; left: 722px; top: 14px; list-style: none; }
  .contacts li {
    display: flex; align-items: center; gap: 14px;
    font-size: 27px; line-height: 38px; color: var(--ink-light);
  }
  .contacts svg { width: 24px; height: 24px; flex: none; }
  .address {
    position: absolute; top: 520px; left: 0; width: 100%;
    text-align: center; font-size: 26px; color: var(--ink-muted); letter-spacing: .5px;
  }
</style>
</head>
<body>
  <main class="card">
    <div class="brand">
      <span class="brand-square"></span>
      <span class="brand-name">BEACON GUARD LLC</span>
    </div>

    <section class="info-band">
      <div class="person">
        <p class="person-name"><span class="first">Mara</span> Velinska</p>
        <p class="person-title">Managing Director</p>
      </div>

      <div class="band-mark">BEACON GUARD</div>

      <ul class="contacts">
        <li>
          <svg viewBox="0 0 24 24" aria-hidden="true"><path fill="#e9e1d4" d="M6.6 10.8a15.1 15.1 0 0 0 6.6 6.6l2.2-2.2c.3-.3.7-.4 1-.2 1.1.4 2.3.6 3.6.6.6 0 1 .4 1 1V20c0 .6-.4 1-1 1A17 17 0 0 1 3 4c0-.6.4-1 1-1h3.5c.6 0 1 .4 1 1 0 1.2.2 2.4.6 3.6.1.3 0 .7-.2 1z"/></svg>
          (555) 214-0386
        </li>
        <li>
          <svg viewBox="0 0 24 24" aria-hidden="true"><rect x="2" y="5" width="20" height="14" rx="1.5" fill="none" stroke="#e9e1d4" stroke-width="2"/><path d="M3 6l9 7 9-7" fill="none" stroke="#e9e1d4" stroke-width="2"/></svg>
          info@beaconguard.com
        </li>
        <li>
          <svg viewBox="0 0 24 24" aria-hidden="true"><circle cx="12" cy="12" r="9.5" fill="none" stroke="#e9e1d4" stroke-width="2"/><path d="M2.5 12h19M12 2.5c3 3 3 16 0 19M12 2.5c-3 3-3 16 0 19" fill="none" stroke="#e9e1d4" stroke-width="1.6"/></svg>
          www.beaconguard.com
        </li>
      </ul>
    </section>

    <p class="address">2480 Harlow Ct #12, Cedar Bay, FL 30418, USA</p>
  </main>
</body>
</html>
```